Business card design needed

Our company background is that we provides transfers to and from the airport, social & corporate events, weddings.
We are also available for charter for birthday party, wine tastings, concerts, anniversary, school balls etc.
Our business cards have to reflect that we have a professional company, they are our first contact and have to stand out from the other 'players' in the market.

Industry/Entity Type

School

Contact Information for Business Card

TELVIK BDR, Lorcan & Mirabel, mob: 0428 351 972, PO Box 847, Kwinana WA 6971, ABN 52 714 309 268, Lic 7164/2918,

Requirements
Must have
• Telephone number: 0428 351 972
Website: www.TELVIKBDR.com.au
postal address: PO Box 847, Kwinana WA 6971
Licences: Lic 7164/2918

***If using the new photo (one with the bus and buildings behind it), if possible can the buildings be cropped out. Thanks
Nice to have
• would be nice to have the pics of the vehicle(s), preferred the Vorn on the card but not too fussed.
Should not have
• Picture of vehicle we don't have in our fleet. (We ONLY have the Vornelles and Korimu Daltra mini bus)

```html
<!DOCTYPE html>
<html lang="en">
<head>
<meta charset="utf-8">
<title>TELVIK BDR – Business Card</title>
<link rel="stylesheet" href="https://fonts.googleapis.com/css2?family=Cinzel:wght@400;600&display=swap">
<style>
  :root {
    --backdrop: #dfe3e4;
    --card: #ffffff;
    --ink: #1c1a1b;
    --band: #231f20;
    --band-text: #f4f2f0;
    --rule: #6b6b6b;
    --photo-light: #cfd3d6;
    --photo-dark: #3b3e42;
  }
  * { box-sizing: border-box; margin: 0; padding: 0; }
  html, body {
    width: 1200px; height: 960px; overflow: hidden;
    background: var(--backdrop);
  }
  .business-card {
    position: absolute; left: 150px; top: 223px;
    width: 900px; height: 514px;
    background: var(--card);
    overflow: hidden;
    box-shadow: 0 10px 30px rgba(0,0,0,0.18);
    font-family: "Cinzel", "Times New Roman", serif;
    color: var(--ink);
  }
  .card-art { position: absolute; inset: 0; }
  .brand {
    position: absolute; left: 58px; top: 72px;
  }
  .brand-name {
    font-size: 50px; font-weight: 400; letter-spacing: 1px; line-height: 1;
    white-space: nowrap;
  }
  .brand-rule {
    margin-top: 10px; width: 300px; height: 1px; background: var(--rule);
  }
  .owners {
    position: absolute; left: 58px; top: 200px;
    font-size: 25px; font-weight: 600; letter-spacing: 0.5px;
    white-space: nowrap;
  }
  .contact {
    position: absolute; left: 58px; top: 318px;
    font-size: 19px; line-height: 38px; list-style: none;
    white-space: nowrap;
  }
  .website {
    position: absolute; right: 34px; bottom: 12px;
    font-size: 20px; color: var(--band-text); letter-spacing: 1px;
    white-space: nowrap;
  }
</style>
</head>
<body>
  <article class="business-card">
    <svg class="card-art" width="900" height="514" viewBox="0 0 900 514">
      <defs>
        <linearGradient id="photoTone" x1="0" y1="0" x2="0" y2="1">
          <stop offset="0" stop-color="var(--photo-light)"/>
          <stop offset="1" stop-color="var(--photo-dark)"/>
        </linearGradient>
        <linearGradient id="photoFade" x1="0" y1="0" x2="1" y2="0">
          <stop offset="0" stop-color="#ffffff" stop-opacity="0.9"/>
          <stop offset="0.2" stop-color="#ffffff" stop-opacity="0"/>
        </linearGradient>
      </defs>
      <g role="img" aria-label="Photo of the company's black luxury sedan">
        <path d="M540 0 H900 V514 H580 C470 420 440 150 540 0 Z" fill="url(#photoTone)"/>
        <path d="M540 0 H900 V514 H580 C470 420 440 150 540 0 Z" fill="url(#photoFade)"/>
      </g>
      <path class="bottom-band" d="M0 490 H570 Q580 490 584 480 L590 466 Q594 456 606 456 H900 V514 H0 Z" fill="var(--band)"/>
    </svg>

    <div class="brand">
      <div class="brand-name">TELVIK BDR</div>
      <div class="brand-rule"></div>
    </div>

    <div class="owners">Lorcan &amp; Mirabel</div>

    <ul class="contact">
      <li>PO Box 847, Kwinana WA 6971</li>
      <li>Tel: 0428 351 972</li>
      <li>Lic 7164/2918 | ABN 52 714 309 268</li>
    </ul>

    <div class="website">www.TELVIKBDR.com.au</div>
  </article>
</body>
</html>
```